Brightfield Ventures Inc. Letterhead

Creation of attractive and eye catching letterhead for a business start-up for the construction industry. Letterhead must relate to construction, but avoid standard hammer and tools in the design.

I forgot to add some details, sorry about that. Some pertinent info: Ph: 916-555-0187 brightfieldventures.example 448 Willowmere Ave, Ste 210 Folsom, CA 95999 info@brightfieldventures.example not sure if slogan should be in there" “Connecting construction professionals to create a purpose driven industry.” must be able to be used in word. Thanks!

```html
<!DOCTYPE html>
<html lang="en">
<head>
<meta charset="utf-8">
<title>Brightfield Ventures Inc. Letterhead</title>
<link rel="stylesheet" href="https://fonts.googleapis.com/css2?family=Open+Sans:wght@400;600;700&display=swap">
<style>
  :root {
    --navy: #101f5a;
    --red: #c00d0d;
    --ink: #2b2b2b;
    --muted: #555;
    --paper: #ffffff;
    --backdrop: #eceeef;
  }
  * { box-sizing: border-box; margin: 0; padding: 0; }
  html, body { width: 1200px; height: 784px; overflow: hidden; }
  body {
    background: var(--backdrop);
    font-family: "Open Sans", Arial, sans-serif;
    color: var(--ink);
    position: relative;
  }
  .letterhead {
    position: absolute;
    left: 338px; top: 22px;
    width: 524px; height: 740px;
    background: var(--paper);
    box-shadow: 0 2px 10px rgba(0,0,0,.12);
    overflow: hidden;
  }
  .brand {
    position: absolute; left: 44px; top: 48px;
    display: flex; align-items: center; gap: 7px;
    font-weight: 700; font-size: 13px; color: var(--navy);
    letter-spacing: .5px; text-transform: uppercase;
  }
  .brand-mark { width: 12px; height: 12px; background: var(--red); }
  .brand-rule {
    position: absolute; left: 44px; top: 72px; width: 150px;
    border-top: 1px solid var(--red);
  }
  .contact {
    position: absolute; right: 40px; top: 40px;
    list-style: none; font-size: 6.5px; line-height: 10px; color: var(--muted);
  }
  .contact li { display: flex; align-items: center; gap: 4px; }
  .contact .dot { width: 4px; height: 4px; border-radius: 50%; background: var(--red); flex: none; }
  .contact .indent { padding-left: 8px; }
  .letter-body {
    position: absolute; left: 56px; top: 124px; width: 400px;
    font-size: 8.6px; line-height: 12.6px;
  }
  .salutation { font-weight: 700; font-size: 10px; margin-bottom: 6px; }
  .letter-body p { margin-bottom: 11px; }
  .signature {
    width: 110px; height: 44px; margin-top: 10px;
    background: linear-gradient(90deg, #f2f2f2, #e2e2e2);
    border-radius: 4px;
  }
  .swoosh { position: absolute; left: 0; bottom: 0; width: 524px; height: 220px; }
</style>
</head>
<body>
  <main class="letterhead">
    <div class="brand"><span class="brand-mark"></span>Brightfield Ventures Inc.</div>
    <div class="brand-rule"></div>

    <ul class="contact">
      <li><span class="dot"></span>Ph: 916-555-0187</li>
      <li><span class="dot"></span>info@brightfieldventures.example</li>
      <li><span class="dot"></span>brightfieldventures.example</li>
      <li class="indent">448 Willowmere Ave, Ste 210</li>
      <li class="indent">Folsom, CA 95999</li>
    </ul>

    <section class="letter-body">
      <p class="salutation">Dear Mr. Alden,</p>
      <p>Lorem Ipsum is simply dummy text of the printing and typesetting industry. Lorem Ipsum has been the industry's standard dummy text ever since the 1500s, when an unknown printer took a galley of type and scrambled it to make a type specimen book. It has survived not only five centuries, but also the leap into electronic typesetting, remaining essentially unchanged.</p>
      <p>The standard chunk of Lorem Ipsum used since the 1500s is reproduced below for those interested. Sections 1.10.32 and 1.10.33 from "de Finibus Bonorum et Malorum" by Cicero are also reproduced in their exact original form, accompanied by English versions from the 1914 translation by H. Rackham.</p>
      <p>Lorem Ipsum is simply dummy text of the printing and typesetting industry. Lorem Ipsum has been the industry's standard dummy text ever since the 1500s, when an unknown printer took a galley of type and scrambled it to make a type specimen book. It has survived not only five centuries, but also the leap into electronic typesetting, remaining essentially unchanged. It was popularised in the</p>
      <p>Lorem Ipsum is simply dummy text of the printing and typesetting industry. Lorem Ipsum has been the industry's standard dummy text ever since the 1500s, when an unknown printer took a galley of type and scrambled it to make a type specimen book. It has survived not only five centuries, but also the leap into electronic typesetting, remaining essentially unchanged. It was popularised in the</p>
      <p>Lorem Ipsum is simply dummy text of the printing and typesetting industry. Lorem Ipsum has been the industry's standard dummy text ever since the 1500s, when an unknown printer took a galley of type and scrambled it to make a type specimen book.</p>
      <div class="signature" role="img" aria-label="Handwritten signature of the sender"></div>
    </section>

    <svg class="swoosh" viewBox="0 0 524 220" preserveAspectRatio="none" aria-hidden="true">
      <path d="M524 0 C470 90 360 170 200 220 L262 220 C400 170 490 100 524 40 Z" fill="var(--red)"/>
      <path d="M524 40 C470 120 350 190 130 220 L200 220 C360 170 470 90 524 0 Z" fill="var(--paper)"/>
      <path d="M524 18 C468 112 350 186 150 220 L172 220 C368 180 478 110 524 32 Z" fill="var(--navy)"/>
    </svg>
  </main>
</body>
</html>
```